Boutique custom software development company needs new business card

Our nearly 20 year old custom software development company would like to better include the fact that we are now providing Bitcoin services. These new services are B2B include education (how to acquire and securely hold Bitcoin) and integrating Bitcoin payments into existing ecommerce sites or other existing systems. Please keep the card clean and simple. Attached is our current design and some other files. vextorial.com

Target Market(s)

businesses owners interested in long term relationship

Industry/Entity Type

Custom software development and Bitcoin

Contact Information for Business Card

Dale Parker, dale@vextorial.com, vextorial.com, (888) 555-VXTRL

Font styles to use
Other font styles liked:
• monospace

Requirements
Must have
• double-sided
Nice to have
• clean and simple
Should not have
• physical address

```html
<!DOCTYPE html>
<html lang="en">
<head>
<meta charset="utf-8">
<title>Vextorial Business Card</title>
<link rel="stylesheet" href="https://fonts.googleapis.com/css2?family=Source+Code+Pro:wght@400;600&family=Source+Sans+3:wght@400;700&display=swap">
<style>
  :root {
    --stage: #5f5e5f;
    --brand-blue: #3f72b6;
    --brand-orange: #f17a24;
    --paper: #ffffff;
    --mono: "Source Code Pro", monospace;
    --sans: "Source Sans 3", sans-serif;
  }
  * { margin: 0; padding: 0; box-sizing: border-box; }
  html, body { width: 1200px; height: 1200px; overflow: hidden; background: var(--stage); }
  .canvas { position: relative; width: 1200px; height: 1200px; }
  .card {
    position: absolute; left: 250px; width: 700px; height: 400px;
    overflow: hidden; box-shadow: 2px 3px 6px rgba(0,0,0,0.35);
  }
  .card-front { top: 170px; background: var(--paper); }
  .card-back { top: 631px; background: var(--brand-blue); }
  .card-shapes { position: absolute; inset: 0; width: 100%; height: 100%; }

  .brand { position: absolute; left: 344px; top: 72px; width: 282px; text-align: center; }
  .brand-name {
    font-family: var(--sans); font-weight: 700; color: var(--brand-blue);
    font-size: 60px; line-height: 1; letter-spacing: 1px; text-transform: uppercase;
  }
  .brand-tagline {
    font-family: var(--sans); font-weight: 400; color: var(--brand-blue);
    font-size: 19.5px; letter-spacing: -0.6px; margin-top: 6px; white-space: nowrap;
  }

  .contact { position: absolute; left: 46px; top: 237px; color: var(--paper); font-family: var(--mono); }
  .contact-name { font-size: 29px; font-weight: 600; letter-spacing: 0.5px; line-height: 1; text-transform: uppercase; margin-bottom: 14px; }
  .contact-list { list-style: none; }
  .contact-item { display: flex; align-items: center; gap: 12px; font-size: 16.5px; height: 24.5px; }
  .contact-icon { width: 14px; height: 14px; flex: none; }

  .services {
    position: absolute; right: 47px; top: 254px; list-style: none;
    font-family: var(--sans); color: var(--paper); font-size: 18.5px; text-align: right;
  }
  .service { display: flex; justify-content: flex-end; align-items: center; gap: 12px; height: 27px; }
  .service::after { content: ""; width: 8px; height: 8px; background: var(--paper); flex: none; }
</style>
</head>
<body>
<main class="canvas">

  <section class="card card-front" aria-label="Business card front">
    <svg class="card-shapes" viewBox="0 0 700 400" preserveAspectRatio="none" aria-hidden="true">
      <polygon points="0,0 513,400 0,400" fill="var(--brand-blue)"/>
      <polygon points="4,0 560,400 520,400" fill="var(--brand-orange)"/>
      <polygon points="2,0 518,400 513,400 0,0" fill="var(--paper)"/>
    </svg>

    <div class="brand">
      <div class="brand-name">Vextorial</div>
      <div class="brand-tagline">developer of custom applications</div>
    </div>

    <div class="contact">
      <h1 class="contact-name">Dale Parker</h1>
      <ul class="contact-list">
        <li class="contact-item">
          <svg class="contact-icon" viewBox="0 0 16 16" aria-hidden="true">
            <path d="M3 1.5l2.5 0 1 3.5-1.6 1.2c.8 1.8 2.2 3.2 4 4l1.2-1.6 3.5 1v2.5c0 .8-.7 1.4-1.5 1.4C6.6 13.5 2.5 9.4 1.5 3c0-.8.6-1.5 1.5-1.5z" fill="var(--paper)"/>
            <path d="M9.5 2.5a4.5 4.5 0 0 1 4 4M9.5 5a2 2 0 0 1 1.6 1.6" stroke="var(--paper)" stroke-width="1.3" fill="none" stroke-linecap="round"/>
          </svg>
          <span>(888) 555-VXTRL</span>
        </li>
        <li class="contact-item">
          <svg class="contact-icon" viewBox="0 0 16 16" aria-hidden="true">
            <rect x="1" y="3.5" width="14" height="9.5" fill="none" stroke="var(--paper)" stroke-width="1.4"/>
            <path d="M1 3.5l7 5.5 7-5.5M1 13l5-4.5M15 13l-5-4.5" fill="none" stroke="var(--paper)" stroke-width="1.2"/>
          </svg>
          <span>dale@vextorial.com</span>
        </li>
        <li class="contact-item">
          <svg class="contact-icon" viewBox="0 0 16 16" aria-hidden="true">
            <circle cx="8" cy="8" r="6.8" fill="none" stroke="var(--paper)" stroke-width="1.4"/>
            <path d="M8 1.2v13.6M1.2 8h13.6M8 1.2c-3 3.5-3 10 0 13.6M8 1.2c3 3.5 3 10 0 13.6" fill="none" stroke="var(--paper)" stroke-width="1"/>
          </svg>
          <span>vextorial.com</span>
        </li>
      </ul>
    </div>
  </section>

  <section class="card card-back" aria-label="Business card back">
    <svg class="card-shapes" viewBox="0 0 700 400" preserveAspectRatio="none" aria-hidden="true">
      <polygon points="0,287 50,263 127,400 0,400" fill="var(--brand-orange)"/>
    </svg>

    <ul class="services">
      <li class="service">Web &amp; Native Applications</li>
      <li class="service">Digital Process Automation</li>
      <li class="service">Cloud-Based Portals</li>
      <li class="service">Bitcoin Consulting</li>
    </ul>
  </section>

</main>
</body>
</html>
```